Etiketten für Olivenöl-Intensivcreme
Zielgruppe
Wir produzieren Bio-Food, u.a. Wein und Olivenöl. Jetzt soll eine Olivenöl-Intensivcreme im Bereich Kosmetik auf dem Markt platziert werden. Unsere Zielgruppe hat ein sehr breites Altersspektrum (jung bis alt), ist naturverbunden, tierlieb, gebildet, kritisch-reflektierend, weiß gute Qualität zu schätzen, ist überwiegend weiblich. Die Olivenöl-Intensivcreme hat eine sehr breite Verwendung und soll sich als 'Allzweckwaffe' in jedem Haushalt etablieren (Babyhaut-Pflege, Lippenpflege, Ganzkörperpflege, Hand-Schutzcreme etc.).
Aufgabenstellung
Die Creme soll heißen: Velamira (es könnte z.B. der Buchstabe 'O' durch eine Olive ersetzt werden). Es gibt zwei Etikette (Deckeloberseite der Metalldose und auf dem Boden). Der Durchmesser der Etikette ist jeweils 5,5 cm. Die Deckelunterseite gilt reinen Pflichtangaben. Im Dateidownloadbereich sind die Textvorgaben für die Etikette. MUT zur Farbe! Wir sind NICHT brav und angepasst! Orange kann Akzente setzen bzw. für Aufmerksamkeit im Regal sorgen.

```html
<!DOCTYPE html>
<html lang="de">
<head>
<meta charset="utf-8">
<title>Velamira – Etiketten</title>
<link rel="stylesheet" href="https://fonts.googleapis.com/css2?family=Kaushan+Script&family=Oswald:wght@400&family=Roboto:wght@400&family=Roboto+Condensed:wght@700&display=swap">
<style>
  :root {
    --bg-light: #ffffff;
    --bg-edge: #d9d9d9;
    --label-white: #ffffff;
    --label-ring: #111111;
    --brand-gold: #b8900a;
    --olive-green: #5b8a2a;
    --olive-dark: #4a6a14;
    --olive-light: #b6cf3a;
    --accent-orange: #e8761a;
    --splash-dark: #b8560c;
    --badge-green: #1e6b12;
    --claim-grey: #8a8a8a;
    --claim-red: #d9480f;
  }
  html, body {
    margin: 0;
    width: 1200px;
    height: 954px;
    overflow: hidden;
  }
  body {
    background: radial-gradient(ellipse at center, var(--bg-light) 45%, var(--bg-edge) 100%);
    position: relative;
  }
  .label {
    position: absolute;
    width: 382px;
    height: 382px;
  }
  .label--lid { left: 185px; top: 112px; }
  .label--base { left: 636px; top: 112px; }
  .label--alt { left: 409px; top: 469px; }
  .brand-name { font-family: "Roboto", Arial, sans-serif; font-size: 28px; fill: var(--brand-gold); }
  .product-name { font-family: "Kaushan Script", cursive; font-size: 104px; fill: var(--olive-green); }
  .product-type { font-family: "Oswald", "Arial Narrow", sans-serif; font-size: 27px; fill: var(--accent-orange); }
  .badge-box { fill: var(--badge-green); }
  .badge-text { font-family: "Oswald", "Arial Narrow", sans-serif; font-size: 26px; fill: var(--label-white); }
  .claim { font-family: "Roboto Condensed", "Arial Narrow", sans-serif; font-weight: 700; font-size: 15px; fill: var(--claim-grey); }
  .claim--red { fill: var(--claim-red); font-size: 16px; }
  .label-face { fill: var(--label-white); }
  .label-ring { fill: none; stroke: var(--label-ring); stroke-width: 2.5; }
</style>
</head>
<body>

<svg class="label label--lid" viewBox="0 0 416 416">
  <defs>
    <clipPath id="lid-clip"><circle cx="208" cy="208" r="207"/></clipPath>
    <linearGradient id="lid-splash" x1="0" y1="0" x2="1" y2="0">
      <stop offset="0" stop-color="var(--splash-dark)"/>
      <stop offset="0.45" stop-color="var(--accent-orange)" stop-opacity="0.85"/>
      <stop offset="1" stop-color="var(--accent-orange)" stop-opacity="0"/>
    </linearGradient>
    <radialGradient id="lid-drops" cx="0.5" cy="0.5" r="0.5">
      <stop offset="0" stop-color="var(--accent-orange)" stop-opacity="0.55"/>
      <stop offset="1" stop-color="var(--accent-orange)" stop-opacity="0"/>
    </radialGradient>
    <radialGradient id="lid-olive" cx="0.45" cy="0.45" r="0.5">
      <stop offset="0" stop-color="var(--olive-light)"/>
      <stop offset="0.7" stop-color="var(--olive-dark)"/>
      <stop offset="1" stop-color="var(--olive-dark)" stop-opacity="0"/>
    </radialGradient>
    <path id="lid-arc" d="M186,387 A180,180 0 0 0 384,171"/>
  </defs>
  <circle class="label-face" cx="208" cy="208" r="207"/>
  <g clip-path="url(#lid-clip)">
    <rect x="0" y="0" width="150" height="416" fill="url(#lid-splash)" role="img" aria-label="Orangefarbener Olivenöl-Spritzer am linken Etikettenrand"/>
    <rect x="260" y="20" width="130" height="150" fill="url(#lid-drops)" role="img" aria-label="Orangefarbene Öltropfen oben rechts"/>
  </g>
  <text class="brand-name" x="215" y="122" text-anchor="middle">MAREVAL.HOF</text>
  <rect x="48" y="145" width="100" height="115" fill="url(#lid-olive)" role="img" aria-label="Grüne Olive mit Blatt als Anfangsbuchstabe"/>
  <text class="product-name" x="148" y="236" textLength="216" lengthAdjust="spacingAndGlyphs">Velamira</text>
  <text class="product-type" x="88" y="280" textLength="246" lengthAdjust="spacingAndGlyphs">OLIVENÖL-INTENSIVCREME</text>
  <rect class="badge-box" x="168" y="286" width="166" height="32"/>
  <text class="badge-text" x="173" y="312" textLength="156" lengthAdjust="spacingAndGlyphs">NATURKOSMETIK</text>
  <text class="claim"><textPath href="#lid-arc">Bio-Olive • Vegan • Pflege - und Schutzcreme</textPath></text>
  <circle class="label-ring" cx="208" cy="208" r="207"/>
</svg>

<svg class="label label--base" viewBox="0 0 416 416">
  <defs>
    <clipPath id="base-clip"><circle cx="208" cy="208" r="207"/></clipPath>
    <linearGradient id="base-splash" x1="0" y1="0" x2="1" y2="0">
      <stop offset="0" stop-color="var(--splash-dark)"/>
      <stop offset="0.45" stop-color="var(--accent-orange)" stop-opacity="0.85"/>
      <stop offset="1" stop-color="var(--accent-orange)" stop-opacity="0"/>
    </linearGradient>
    <radialGradient id="base-drops" cx="0.5" cy="0.5" r="0.5">
      <stop offset="0" stop-color="var(--accent-orange)" stop-opacity="0.55"/>
      <stop offset="1" stop-color="var(--accent-orange)" stop-opacity="0"/>
    </radialGradient>
    <radialGradient id="base-olive" cx="0.45" cy="0.45" r="0.5">
      <stop offset="0" stop-color="var(--olive-light)"/>
      <stop offset="0.7" stop-color="var(--olive-dark)"/>
      <stop offset="1" stop-color="var(--olive-dark)" stop-opacity="0"/>
    </radialGradient>
  </defs>
  <circle class="label-face" cx="208" cy="208" r="207"/>
  <g clip-path="url(#base-clip)">
    <rect x="0" y="0" width="150" height="416" fill="url(#base-splash)" role="img" aria-label="Orangefarbener Olivenöl-Spritzer am linken Etikettenrand"/>
    <rect x="260" y="20" width="130" height="150" fill="url(#base-drops)" role="img" aria-label="Orangefarbene Öltropfen oben rechts"/>
  </g>
  <text class="brand-name" x="215" y="122" text-anchor="middle">MAREVAL.HOF</text>
  <rect x="48" y="145" width="100" height="115" fill="url(#base-olive)" role="img" aria-label="Grüne Olive mit Blatt als Anfangsbuchstabe"/>
  <text class="product-name" x="148" y="236" textLength="216" lengthAdjust="spacingAndGlyphs">Velamira</text>
  <text class="product-type" x="88" y="280" textLength="246" lengthAdjust="spacingAndGlyphs">OLIVENÖL-INTENSIVCREME</text>
  <rect class="badge-box" x="144" y="286" width="190" height="32"/>
  <text class="badge-text" x="168" y="312" textLength="156" lengthAdjust="spacingAndGlyphs">NATURKOSMETIK</text>
  <text class="claim" x="332" y="337" text-anchor="end">Pflege - und Schutzcreme</text>
  <text class="claim" x="328" y="357" text-anchor="end">• Bio-Olive • Vegan</text>
  <circle class="label-ring" cx="208" cy="208" r="207"/>
</svg>

<svg class="label label--alt" viewBox="0 0 416 416">
  <defs>
    <clipPath id="alt-clip"><circle cx="208" cy="208" r="207"/></clipPath>
    <linearGradient id="alt-splash" x1="0" y1="0" x2="1" y2="0">
      <stop offset="0" stop-color="var(--splash-dark)"/>
      <stop offset="0.45" stop-color="var(--accent-orange)" stop-opacity="0.85"/>
      <stop offset="1" stop-color="var(--accent-orange)" stop-opacity="0"/>
    </linearGradient>
    <radialGradient id="alt-drops" cx="0.5" cy="0.5" r="0.5">
      <stop offset="0" stop-color="var(--accent-orange)" stop-opacity="0.55"/>
      <stop offset="1" stop-color="var(--accent-orange)" stop-opacity="0"/>
    </radialGradient>
    <radialGradient id="alt-olive" cx="0.45" cy="0.45" r="0.5">
      <stop offset="0" stop-color="var(--olive-light)"/>
      <stop offset="0.7" stop-color="var(--olive-dark)"/>
      <stop offset="1" stop-color="var(--olive-dark)" stop-opacity="0"/>
    </radialGradient>
    <path id="alt-arc" d="M186,387 A180,180 0 0 0 384,171"/>
  </defs>
  <circle class="label-face" cx="208" cy="208" r="207"/>
  <g clip-path="url(#alt-clip)">
    <rect x="0" y="0" width="150" height="416" fill="url(#alt-splash)" role="img" aria-label="Orangefarbener Olivenöl-Spritzer am linken Etikettenrand"/>
    <rect x="260" y="20" width="130" height="150" fill="url(#alt-drops)" role="img" aria-label="Orangefarbene Öltropfen oben rechts"/>
  </g>
  <text class="brand-name" x="215" y="122" text-anchor="middle">MAREVAL.HOF</text>
  <rect x="48" y="145" width="100" height="115" fill="url(#alt-olive)" role="img" aria-label="Grüne Olive mit Blatt als Anfangsbuchstabe"/>
  <text class="product-name" x="148" y="236" textLength="216" lengthAdjust="spacingAndGlyphs">Velamira</text>
  <text class="product-type" x="88" y="280" textLength="246" lengthAdjust="spacingAndGlyphs">OLIVENÖL-INTENSIVCREME</text>
  <rect class="badge-box" x="168" y="286" width="166" height="32"/>
  <text class="badge-text" x="173" y="312" textLength="156" lengthAdjust="spacingAndGlyphs">NATURKOSMETIK</text>
  <text class="claim claim--red"><textPath href="#alt-arc">Bio-Olive • Vegan • Pflege - und Schutzcreme</textPath></text>
  <circle class="label-ring" cx="208" cy="208" r="207"/>
</svg>

</body>
</html>
```